Korval Advise Business Cards

We need a business card design for Korval Advise (Logo Attached), a management consultancy specialized in brand & business building.

Design should be clean, smart and a touch of innnovation without being gimmicky.

The details on the card should be:
Name: Tomas Velduren
Title: Managing Director
Address: 42 Marlowe Pier, Tarn Vessel Tower, Singapore 073926
Tel: +6285927461082
email: tv@korvaladvise.example
website: korvaladvise.example

For further background on corporate identity, please check www.korvaladvise.example
Updates

Dear all,

Many thanks for the submissions so far! I gave feedback to those designs that I prefer at this stage.

Overall I see that my preference goes into the direction that 'less is more' and 'simple is beautiful'

Please create uniqueness and standout by the simplicity and attraction of the overall concept and design.

Many thanks and please shout incase of questions!

Tomas

Industry/Entity Type

Business

```html
<!DOCTYPE html>
<html lang="en">
<head>
<meta charset="utf-8">
<title>Korval Advise Business Cards</title>
<link rel="stylesheet" href="https://fonts.googleapis.com/css2?family=Open+Sans:wght@400;600;700&display=swap">
<style>
  :root {
    --backdrop: #efefef;
    --card-white: #ffffff;
    --charcoal: #4a4a4a;
    --ink: #3a3a3a;
    --orange: #f07b1f;
    --rule-grey: #9a9a9a;
    --on-dark: #ffffff;
  }
  * { margin: 0; padding: 0; box-sizing: border-box; }
  html, body {
    width: 1175px;
    height: 1200px;
    overflow: hidden;
    background: var(--backdrop);
    font-family: "Open Sans", Arial, sans-serif;
  }
  .canvas { position: relative; width: 1175px; height: 1200px; }

  .card { position: absolute; overflow: hidden; }

  /* Front */
  .card-front {
    left: 186px; top: 46px; width: 941px; height: 537px;
    background: var(--card-white);
    box-shadow: 0 2px 6px rgba(0,0,0,0.18);
  }
  .front-wordmark {
    position: absolute; left: 0; right: 0; top: 58px;
    text-align: center;
    font-size: 80px; font-weight: 600; line-height: 1.2;
    color: var(--ink);
    white-space: nowrap;
  }
  .address {
    position: absolute; right: 510px; top: 258px;
    text-align: right;
    font-style: normal;
    font-size: 23px; line-height: 42px;
    color: var(--ink);
    white-space: nowrap;
  }
  .divider {
    position: absolute; left: 451px; top: 250px;
    width: 1px; height: 135px;
    background: var(--rule-grey);
  }
  .contacts {
    position: absolute; left: 479px; top: 258px;
    list-style: none;
    font-size: 23px; line-height: 42px;
    color: var(--ink);
    white-space: nowrap;
  }
  .contacts li { display: flex; align-items: center; gap: 9px; height: 47px; }
  .contacts svg { width: 18px; height: 18px; flex: none; }
  .accent-rule {
    position: absolute; left: 0; right: 0; top: 466px;
    height: 4px; background: var(--orange);
  }
  .name-band {
    position: absolute; left: 0; right: 0; top: 478px; bottom: 0;
    background: var(--charcoal);
    color: var(--on-dark);
    display: flex; align-items: center; justify-content: center;
    font-size: 23px;
    white-space: nowrap;
  }
  .name-band .person { font-weight: 700; font-size: 28px; margin-right: 8px; }

  /* Back */
  .card-back {
    left: 46px; top: 612px; width: 943px; height: 537px;
    background: var(--charcoal);
  }
  .back-wordmark {
    position: absolute; left: 0; right: 0; top: 205px;
    text-align: center;
    font-size: 100px; font-weight: 600; line-height: 1.2;
    color: var(--on-dark);
    white-space: nowrap;
  }
  .back-web {
    position: absolute; left: 0; right: 0; top: 412px;
    text-align: center;
    font-size: 26px; letter-spacing: 4px;
    color: var(--on-dark);
    white-space: nowrap;
  }
</style>
</head>
<body>
<div class="canvas">

  <section class="card card-front">
    <div class="front-wordmark">Korval Advise</div>

    <address class="address">
      42 Marlowe Pier,<br>
      Tarn Vessel Tower<br>
      Singapore 073926
    </address>

    <div class="divider"></div>

    <ul class="contacts">
      <li>
        <svg viewBox="0 0 20 20" aria-hidden="true">
          <circle cx="10" cy="10" r="9" fill="none" stroke="#f07b1f" stroke-width="2"/>
          <path d="M7 5.5c-1 1-1 3 .5 5.5s3.5 4 5 4l1.3-1.5-2-1.7-1 .8c-1-.6-2-1.8-2.5-3l.9-1-1.3-2.3z" fill="#f07b1f"/>
        </svg>
        +6285927461082
      </li>
      <li>
        <svg viewBox="0 0 20 20" aria-hidden="true">
          <rect x="1" y="4" width="18" height="12" rx="1.5" fill="#f07b1f"/>
          <path d="M2 5l8 6 8-6" fill="none" stroke="#ffffff" stroke-width="1.6"/>
        </svg>
        tv@korvaladvise.example
      </li>
      <li>
        <svg viewBox="0 0 20 20" aria-hidden="true">
          <g fill="none" stroke="#f07b1f" stroke-width="1.6">
            <circle cx="10" cy="10" r="8.5"/>
            <ellipse cx="10" cy="10" rx="3.8" ry="8.5"/>
            <path d="M1.5 10h17M3 5.5h14M3 14.5h14"/>
          </g>
        </svg>
        www.korvaladvise.example
      </li>
    </ul>

    <div class="accent-rule"></div>
    <div class="name-band">
      <span class="person">Tomas Velduren,</span>
      <span class="role">Managing Director</span>
    </div>
  </section>

  <section class="card card-back">
    <div class="back-wordmark">Korval Advise</div>
    <div class="back-web">www.korvaladvise.example</div>
  </section>

</div>
</body>
</html>
```